Harborline Auto LLC

Car Dealer Customer Service
Address: 2874 Cresthaven Road, Shelbyville, TN 37162
web: www.harborlineautoxq.net
email: harborlineautoxq@mailnest.example
Phone: (931) 555-0148
Phone: (629) 555-0173

```html
<!DOCTYPE html>
<html lang="en">
<head>
<meta charset="utf-8">
<title>Harborline Auto – Business Card</title>
<link rel="stylesheet" href="https://fonts.googleapis.com/css2?family=Montserrat:wght@400;600;700&display=swap">
<style>
  :root {
    --backdrop: #1d1d1f;
    --card: #f7f7f5;
    --brand-blue: #1d7fb8;
    --brand-gold: #f2b33d;
    --ink: #555559;
    --rule: #8a8a8e;
  }
  * { box-sizing: border-box; margin: 0; padding: 0; }
  html, body {
    width: 1200px; height: 963px; overflow: hidden;
    background: var(--backdrop);
    font-family: "Montserrat", sans-serif;
  }
  .stage {
    width: 1200px; height: 963px;
    display: flex; align-items: center; justify-content: center;
  }
  .business-card {
    position: relative;
    width: 840px; height: 480px;
    background: var(--card);
    box-shadow: 0 18px 40px rgba(0,0,0,.55);
  }
  .brand {
    position: absolute; right: 56px; top: 150px;
    display: flex; align-items: center; gap: 14px;
  }
  .brand-dot {
    width: 30px; height: 30px; border-radius: 50%;
    background: var(--brand-gold);
  }
  .brand-name {
    font-weight: 700; font-size: 34px; letter-spacing: .5px;
    color: var(--brand-blue); text-transform: uppercase;
  }
  .holder {
    position: absolute; left: 64px; top: 150px;
  }
  .holder-name {
    font-weight: 700; font-size: 26px; color: var(--brand-blue);
    text-transform: uppercase; letter-spacing: .5px;
  }
  .holder-role {
    font-size: 17px; color: var(--ink); margin-top: 2px;
  }
  .divider {
    position: absolute; left: 54px; top: 232px;
    width: 600px; height: 1px; background: var(--rule);
  }
  .contact {
    position: absolute; left: 64px; top: 250px;
    font-size: 16px; color: var(--ink); line-height: 1;
  }
  .contact-row { display: flex; align-items: center; gap: 26px; margin-bottom: 16px; }
  .contact-item { display: flex; align-items: center; gap: 8px; }
  .icon { width: 18px; height: 18px; flex: none; }
</style>
</head>
<body>
<main class="stage">
  <section class="business-card" aria-label="Harborline Auto business card">
    <div class="brand">
      <span class="brand-dot"></span>
      <span class="brand-name">Harborline Auto</span>
    </div>

    <div class="holder">
      <p class="holder-name">Marcus Delaney</p>
      <p class="holder-role">Manager</p>
    </div>

    <div class="divider"></div>

    <div class="contact">
      <div class="contact-row">
        <span class="contact-item">2874 Cresthaven Road, Shelbyville, TN 37162</span>
      </div>
      <div class="contact-row">
        <span class="contact-item">
          <svg class="icon" viewBox="0 0 20 20"><circle cx="10" cy="10" r="10" fill="var(--brand-blue)"/><path d="M7 5.5l1.6 2.4-1 1.2a6 6 0 0 0 3.3 3.3l1.2-1 2.4 1.6-.9 1.6c-3.8-.2-7-3.4-7.2-7.2z" fill="#fff"/></svg>
          (931) 555-0148
        </span>
        <span class="contact-item">
          <svg class="icon" viewBox="0 0 20 20"><circle cx="10" cy="10" r="10" fill="var(--brand-blue)"/><path d="M7 5.5l1.6 2.4-1 1.2a6 6 0 0 0 3.3 3.3l1.2-1 2.4 1.6-.9 1.6c-3.8-.2-7-3.4-7.2-7.2z" fill="#fff"/></svg>
          (629) 555-0173
        </span>
      </div>
      <div class="contact-row">
        <span class="contact-item">
          <svg class="icon" viewBox="0 0 20 20"><circle cx="10" cy="10" r="10" fill="var(--brand-blue)"/><rect x="5" y="6.5" width="10" height="7" fill="#fff"/><path d="M5 6.5l5 4 5-4" fill="none" stroke="var(--brand-blue)" stroke-width="1.2"/></svg>
          harborlineautoxq@mailnest.example
        </span>
        <span class="contact-item">
          <svg class="icon" viewBox="0 0 20 20"><circle cx="10" cy="10" r="10" fill="var(--brand-blue)"/><circle cx="10" cy="10" r="5.5" fill="none" stroke="#fff" stroke-width="1.3"/><path d="M4.5 10h11M10 4.5c-2.5 3-2.5 8 0 11M10 4.5c2.5 3 2.5 8 0 11" fill="none" stroke="#fff" stroke-width="1.1"/></svg>
          www.harborlineautoxq.net
        </span>
      </div>
    </div>
  </section>
</main>
</body>
</html>
```